Tessmar Fahrwerkstatt
Sehr angenehme zusammenarbeit nicht aufdringlich und genau auf die Wünsche eingegangen. Wir werde sicher noch mehr zusammen Arbeiten. Gruss Lukas Hegemann Inhaber Tessmar Fahrwerkstatt
Zielgruppe
Dinks und Kunden mit viel Erfolg und hohem Ausgabepotential.
Aufgabenstellung
Unsere Firma vertreibt Fahrzeuge im Luxusbereich hauptgebiet Valmerra aber auch andere Sportwagen. Was uns fehlt ist ein optischer Wiedererkennugswert. Deshalb hätten wir gerne ein Visitenkarten Design und Briefpapier Design. Später soll auch noch eine Webseite mit gleichem Wiedererkennungswert entstehen. " Roter Faden "

```html
<!DOCTYPE html>
<html lang="de">
<head>
<meta charset="utf-8">
<title>Tessmar Fahrwerkstatt – Briefpapier und Visitenkarte</title>
<link rel="stylesheet" href="https://fonts.googleapis.com/css2?family=Open+Sans:wght@300;400;700&display=swap">
<style>
  :root {
    --paper: #ffffff;
    --band: #4a514e;
    --ink: #4a514e;
    --text: #8c8f8e;
    --accent: #f2b34a;
    --card-edge: #d8d8d8;
  }
  * { margin: 0; padding: 0; box-sizing: border-box; }
  html, body { width: 848px; height: 1200px; overflow: hidden; background: var(--paper); }
  body { font-family: "Open Sans", Arial, sans-serif; color: var(--text); }

  .letterhead { position: relative; width: 848px; height: 1200px; background: var(--paper); }
  .swoosh { position: absolute; left: 0; top: 0; width: 848px; height: 200px; }

  .wordmark {
    position: absolute; display: flex; align-items: center; gap: 14px;
    font-family: "Open Sans", Arial, sans-serif; font-weight: 700; color: var(--ink);
    line-height: 1.02;
  }
  .wordmark .dot { flex: none; border-radius: 50%; background: var(--accent); }
  .letterhead > .wordmark { left: 278px; top: 30px; font-size: 33px; }
  .letterhead > .wordmark .dot { width: 62px; height: 62px; }

  .sender-line { position: absolute; left: 47px; top: 207px; font-size: 10.5px; font-weight: 300; }

  .card {
    position: absolute; width: 346px; height: 230px;
    background: var(--paper); border: 1px solid var(--card-edge); overflow: hidden;
  }
  .card-front { left: 40px; top: 362px; }
  .card-front .band { position: absolute; left: 0; top: 0; width: 346px; height: 230px; }
  .card-front .wordmark { left: 44px; top: 48px; font-size: 25px; gap: 12px; }
  .card-front .wordmark .dot { width: 46px; height: 46px; }

  .card-back { left: 40px; top: 634px; }
  .card-back .contact { position: absolute; left: 106px; top: 28px; font-size: 12px; }

  .contact { font-weight: 300; line-height: 1.28; }
  .contact .name { font-weight: 400; font-size: 1.1em; margin-bottom: 1.1em; }
  .contact .block { margin-bottom: 1.1em; }
  .contact dl { display: grid; grid-template-columns: 4em auto; }
  .card-back .contact dl { grid-template-columns: 3.8em auto; }

  .page-contact { position: absolute; left: 601px; top: 884px; font-size: 12.3px; }
</style>
</head>
<body>
<main class="letterhead">
  <svg class="swoosh" viewBox="0 0 848 200" aria-hidden="true">
    <path d="M0,52 Q380,178 822,82 Q420,214 0,93 Z" fill="var(--band)"/>
  </svg>

  <div class="wordmark"><span class="dot"></span><span>Tessmar<br>Fahrwerkstatt</span></div>

  <p class="sender-line">Tessmar Fahrwerkstatt • Lindenhofweg 145 • 54321 Hellbrunn</p>

  <section class="card card-front">
    <svg class="band" viewBox="0 0 346 230" aria-hidden="true">
      <path d="M0,132 Q190,128 346,104 L346,132 Q190,156 0,168 Z" fill="var(--band)"/>
    </svg>
    <div class="wordmark"><span class="dot"></span><span>Tessmar<br>Fahrwerkstatt</span></div>
  </section>

  <section class="card card-back">
    <div class="contact">
      <p class="name">Tessmar Fahrwerkstatt</p>
      <p class="block">Lindenhofweg 45<br>54321 Hellbrunn</p>
      <dl class="block">
        <dt>tel.:</dt><dd>+49.241.508.72.14</dd>
        <dt>fax.:</dt><dd>+49.241.508.72.149</dd>
        <dt>mobil:</dt><dd>+49.171.604.38.92</dd>
      </dl>
      <p>info@tessmar-fahrwerkstatt.de<br>www.tessmar-fahrwerkstatt.de</p>
    </div>
  </section>

  <address class="contact page-contact" style="font-style: normal;">
    <p class="name">Tessmar Fahrwerkstatt</p>
    <p class="block">Lindenhofweg 45<br>54321 Hellbrunn</p>
    <dl class="block">
      <dt>tel.:</dt><dd>+49.241.508.72.14</dd>
      <dt>fax.:</dt><dd>+49.241.508.72.149</dd>
      <dt>mobil:</dt><dd>+49.171.604.38.92</dd>
    </dl>
    <p class="block">info@tessmar-fahrwerkstatt.de<br>www.tessmar-fahrwerkstatt.de</p>
    <p>bank</p>
    <dl class="block">
      <dt>blz.:</dt><dd>482.615.09</dd>
      <dt>kto.:</dt><dd>740.218.563</dd>
      <dt>iban:</dt><dd>DE41482615090740218563</dd>
      <dt>swift:</dt><dd>HELBDEXXKRF</dd>
    </dl>
    <p>Umst.nr.: 318/4071/5926</p>
  </address>
</main>
</body>
</html>
```